Nutritional & Gastrointestinal Health Consulting Service-Website design

We need a website design for a new health consulting service called "Bright Vale" based in Perth, Australia.

We will be providing consulting services in the areas of:
1) Nutrition and Diet
2) Gastrointestinal Health (which means stomach & digestive system related health)

These consulting services will be provided by an Accredited Dietitian and a Paediatric Gastroenterologist.

We are open to creative ideas in terms of design, layout, fonts and colours. We also would love to see images of nature in the backdrop with families (adults with kids) having a good time, fresh fruits and vegetables displayed in a farmer's market or supermarket. 2 or 3 images should be sufficient. We would also definitely want our logo somewhere in the main page of website. The logo file is also attached. Please have a look at a website's design that we really liked. We would love to see designs inspired by that style. The website details are in the in the "nice to have priorities" section of this project brief.

We also would be looking at website designers with software coding skills so that if we like the design we can go ahead with the next step of coding.

The website design should communicate the purpose of the website and at the same time be simple, elegant and unique/eye-catching.

We look forward to receiving creative ideas for our website from you all. Good luck!

More details have been added to our project- for example: Logo, fonts style, must haves etc etc. Please view the updated project brief. Looking forward to receiving your fantastic ideas for our website. Thanking you

Hi, I have updated the colour preference. Will add the content preferences tomorrow. thanks

Hello all, I have now added a LOT more content to what we want in our website. It is very much in detail, so please carefully have a read through the entire project brief. If you have any questions write back to me and I will try to respond as quickly as I can. Last few days were busy so couldn't respond quickly to all of you who had send me designs/queries/questions. Thank you for your patience. I look forward to receiving fantastic designs from you all. Good Luck :-)

Target Market(s)

Adults based in western speaking countries aged 18 to 60 years

Industry/Entity Type

Software

Font styles to use
Sans Serif
Script

Colors
faa54b
acd036

Requirements
Must have
• The website must have the MAIN logo file attached. I have attached 3 files: 1) MAIN logo; 2) supplementary logo A ; 3) supplementary logo B

I have selected 2 colours from the colour scheme (see below)-(as the colour of our logo is that).
However we would also like to see LIGHT CHOCOLATE BROWN or CHOCOLATE BROWN colour used as the background colour of the website
Preferred WEBSITE CONTENT:
1) HOME PAGE:
Content required=
--Company Logo
--Dr Dorian Pelham
Paediatric Gastroenterologist & Hepatologist
-Marla Pelham.
Dietitian & Nutritionist
--Website Menu (either listed horizontally or vertically):
Once clicked on each name:

Under each of the Website Menu items we want the following Headings to be added

2) ABOUT US page:
Sub-heading under this: Qualification, Skills, Special Interest

3) SERVICES
DORIAN'S PAGE: Individual Consultation, Endoscopy procedures
Individual Consultation, Group Based Services, Food Diary, Food & Symptom Diary

4) FEES & REBATE: Content as below:
Please Note: Payment of full fees is required at the time of consultation and procedures. 48 hours notice is required for cancellation of appointments/non-attendance. Failure to provide this may result in a fee being incurred. Please call reception to find out the amount of fee charged for cancellation of appointments/non-attendance.
headings are:
Paediatric Gastroenterology:
Dorian's pge
Individual Consultation - Initial (upto 30 mins):
Review Consultation (upto 15 mins):
Endoscopy procedures - No Gap fees charged. Fees will be billed directly to Vitacover. If any queries, please contact reception.

marla's pge
sub heading:
Individual Consultation - Initial (upto 45 mins):
Individual Consultation - Review (upto 30 mins):

Concession-Individual Consultation -Initial (upto 45 mins):
Concession-Individual Consultation - Review (upto 30 mins):
Please Note: Concession applies for health care card holders & pensioners

Group Based Services: Pricing subject to the type of service provided. Please contact us for an obligation free quote.
Education Topics Include:
- Paediatric Nutrition (Introducing Solids, Fussy Eating, Healthy Eating)
- Pregnancy Nutrition, Gestational Diabetes, Breastfeeding/Lactation Nutrition
- Healthy Eating, Supermarket Shopping Tips, Nutrition Label Reading Tips, Healthier
sub heading under nutrition & diet:
-Vitacover:
--A rebate of $52.95 is available from Vitacover if an EPC ( Enhanced Primary Care)/Chronic Disease Management (CDM) plan is issued by your GP.
--All mandatory paperwork needs to be available at the time of making your appointment for your eligibility.
-Private Health Fund:
--Most private health funds provide rebate on dietetic appointments. However the rebate amount depends on your level of cover. Thus, please contact your health fund to determine your entitled rebate.
-RSB: Approved provider for RSB services

6) FOR DOCTORS: Bright Vale Paediatric Gastroenterologist Referral Form
Bright Vale Dietitian Referral form
7) LOCATIONS & CONTACT

Paediatric Gastroenterology & Hepatology Service
Suite 46
Holy Lantern Bramcote Medical Centre
17 Colin Ferris Pde,
MURDOCH, WA 6150
P: (08) 9422 5061
F: (08) 9422 3094

Nutrition & Diet Service
Suite 46
17 Colin Ferris Pde,
MURDOCH, WA 6150
P: (08) 9422 5061
F: (08) 9422 3094

Tolland Medical Centre
58-60 Karrigan Parkway,
MANDURAH, WA 6210
P: (08) 9647 2283
F: (08) 96724419
www.tmcexample.com.au

This page should have a webform that has following titles:
-Your Name
-Your Email
-Your Phone
-Message

8) NEWS & BLOG
Nice to have
• We liked the design style of the websites below:
https://www.vendoraplex.example/

http://qoravelt.example/

But feel free to use your creativity too
Should not have
• Please do not use any body building or muscle building images

```html
<!DOCTYPE html>
<html lang="en">
<head>
<meta charset="utf-8">
<title>Bright Vale — Nutrition &amp; Gastroenterology</title>
<link href="https://fonts.googleapis.com/css2?family=Open+Sans:wght@400;700;800&display=swap" rel="stylesheet">
<style>
  :root {
    --brown-deep: #472a25;
    --brown-mid: #54322c;
    --brown-warm: #7a463b;
    --band: rgba(22, 12, 10, 0.62);
    --orange: #faa54b;
    --green: #acd036;
    --white: #ffffff;
    --muted: #e9e1de;
  }
  * { box-sizing: border-box; margin: 0; padding: 0; }
  html, body { width: 1200px; height: 863px; overflow: hidden; }
  body {
    font-family: "Open Sans", sans-serif;
    color: var(--white);
    background:
      radial-gradient(ellipse 700px 500px at 1200px 0, var(--brown-warm), transparent 70%),
      linear-gradient(180deg, var(--brown-deep) 0%, var(--brown-mid) 100%);
    position: relative;
  }
  .practitioner {
    position: absolute;
    top: 120px;
    width: 360px;
    text-align: center;
    font-size: 15px;
    line-height: 21px;
  }
  .practitioner--left { left: 139px; }
  .practitioner--right { left: 688px; }
  .practitioner__name strong { font-weight: 800; }
  .brand-disc {
    position: absolute;
    left: 492px;
    top: 150px;
    width: 260px;
    height: 260px;
    border-radius: 50%;
    background: var(--orange);
    box-shadow: 0 14px 30px rgba(0,0,0,0.45);
  }
  .main-nav {
    position: absolute;
    left: 0;
    top: 370px;
    width: 1200px;
    height: 126px;
    background: var(--band);
  }
  .main-nav__item {
    position: absolute;
    top: 22px;
    width: 130px;
    margin-left: -65px;
    text-align: center;
    text-decoration: none;
    color: var(--white);
  }
  .main-nav__icon { display: block; margin: 0 auto 6px; width: 34px; height: 34px; }
  .main-nav__title {
    display: block;
    font-weight: 800;
    font-size: 14px;
    line-height: 14px;
    text-transform: uppercase;
  }
  .main-nav__sub {
    display: block;
    font-size: 13px;
    line-height: 17px;
    color: var(--muted);
    text-transform: uppercase;
  }
  .wordmark {
    position: absolute;
    left: 0;
    top: 560px;
    width: 1200px;
    text-align: center;
    font-weight: 800;
    font-size: 118px;
    line-height: 118px;
    letter-spacing: 4px;
    color: var(--green);
    text-transform: uppercase;
  }
</style>
</head>
<body>
  <header>
    <div class="practitioner practitioner--left">
      <p class="practitioner__name"><strong>DR DORIAN</strong> PELHAM</p>
      <p class="practitioner__role">Paediatric Gastroenterologist &amp; Hepatologist</p>
    </div>
    <div class="practitioner practitioner--right">
      <p class="practitioner__name"><strong>MARLA</strong> PELHAM</p>
      <p class="practitioner__role">Accredited Practising Dietitian</p>
    </div>
    <div class="brand-disc" aria-hidden="true"></div>
  </header>

  <nav class="main-nav">
    <a class="main-nav__item" href="#" style="left:147px">
      <svg class="main-nav__icon" viewBox="0 0 34 34" fill="var(--orange)">
        <circle cx="13" cy="10" r="7"/>
        <path d="M1 30c0-8 5-12 12-12s12 4 12 12z"/>
        <circle cx="25" cy="21" r="7" stroke="#2a1a17" stroke-width="2"/>
        <text x="25" y="25" font-size="10" font-weight="700" text-anchor="middle" fill="#2a1a17" font-family="Open Sans, sans-serif">?</text>
      </svg>
      <span class="main-nav__title">About<br>Us</span>
    </a>
    <a class="main-nav__item" href="#" style="left:274px">
      <svg class="main-nav__icon" viewBox="0 0 34 34" fill="none" stroke="var(--orange)" stroke-width="3">
        <rect x="7" y="5" width="20" height="26" rx="2"/>
        <path d="M12 13h10M12 19h10M12 25h6"/>
      </svg>
      <span class="main-nav__title">Nutrition &amp;<br>Diet</span>
      <span class="main-nav__sub">Services</span>
    </a>
    <a class="main-nav__item" href="#" style="left:400px">
      <svg class="main-nav__icon" viewBox="0 0 34 34">
        <circle cx="17" cy="17" r="14" fill="var(--orange)"/>
        <path d="M17 9v16M9 17h16" stroke="#2a1a17" stroke-width="4"/>
      </svg>
      <span class="main-nav__title">Gastro-<br>Enterology</span>
      <span class="main-nav__sub">Services</span>
    </a>
    <a class="main-nav__item" href="#" style="left:820px">
      <svg class="main-nav__icon" viewBox="0 0 34 34" fill="var(--orange)">
        <ellipse cx="13" cy="13" rx="12" ry="9"/>
        <path d="M5 19l-2 7 8-4z"/>
        <ellipse cx="23" cy="21" rx="9" ry="7" stroke="#2a1a17" stroke-width="2"/>
        <path d="M28 26l4 5-8-3z"/>
      </svg>
      <span class="main-nav__title">Blog</span>
      <span class="main-nav__sub">&amp; News</span>
    </a>
    <a class="main-nav__item" href="#" style="left:924px">
      <svg class="main-nav__icon" viewBox="0 0 34 34" fill="none" stroke="var(--orange)" stroke-width="2.5">
        <rect x="4" y="8" width="26" height="19"/>
        <path d="M4 8l13 11 13-11"/>
      </svg>
      <span class="main-nav__title">Contact</span>
      <span class="main-nav__sub">Us</span>
    </a>
    <a class="main-nav__item" href="#" style="left:1043px">
      <svg class="main-nav__icon" viewBox="0 0 34 34">
        <path d="M18 3h11v11L14 31 3 20z" fill="var(--orange)"/>
        <circle cx="24" cy="9" r="2.5" fill="#2a1a17"/>
      </svg>
      <span class="main-nav__title">Fees &amp;</span>
      <span class="main-nav__sub">Rebate</span>
    </a>
  </nav>

  <h1 class="wordmark">Bright<br>Vale</h1>
</body>
</html>
```